Business Card Design Project

Looking to update our business cards. We have a logo with our slogan. We are an IT firm so we wouldlike a modern look.

Industry/Entity Type

Business

```html
<!DOCTYPE html>
<html lang="en">
<head>
<meta charset="utf-8">
<title>Corelane Business Card Concepts</title>
<link rel="stylesheet" href="https://fonts.googleapis.com/css2?family=Source+Sans+3:wght@400;600;700&display=swap">
<style>
  :root {
    --stage: #e8e4de;
    --label: #2a2622;
    --card-dark: #050505;
    --card-light: #ffffff;
    --card-lime: #b1c146;
    --brand-green: #6a8a3b;
    --tagline-dark: #222222;
    --text-light: #ffffff;
    --rule: #8a8a8a;
    --photo-deep: #13236e;
    --photo-mid: #3f6fd0;
    --photo-glow: #e6f2ff;
  }
  * { box-sizing: border-box; margin: 0; padding: 0; }
  html, body { width: 1200px; height: 788px; overflow: hidden; }
  body {
    position: relative;
    background: var(--stage);
    font-family: "Source Sans 3", "Myriad Pro", Arial, sans-serif;
  }
  .view-label {
    position: absolute;
    width: 525px;
    text-align: center;
    font-size: 22px;
    font-weight: 400;
    color: var(--label);
  }
  .card {
    position: absolute;
    width: 525px;
    height: 298px;
    border-radius: 22px;
    overflow: hidden;
  }
  .card--front { left: 50px; top: 82px; background: var(--card-dark); color: var(--text-light); }
  .card--back-white { left: 620px; top: 80px; background: var(--card-light); }
  .card--back-lime { left: 50px; top: 455px; background: var(--card-lime); }
  .card--back-photo { left: 620px; top: 455px; }

  .photo-fill {
    position: absolute; inset: 0;
    background:
      radial-gradient(ellipse 42% 48% at 50% 55%, var(--photo-glow) 0%, rgba(190,215,255,.85) 30%, rgba(90,140,230,.4) 60%, transparent 80%),
      linear-gradient(100deg, var(--photo-deep) 0%, var(--photo-mid) 45%, #9aa7e8 65%, var(--photo-deep) 100%);
  }

  .brand {
    position: absolute;
    left: 0; right: 0;
    text-align: center;
  }
  .brand-name {
    display: inline-flex;
    align-items: center;
    gap: 12px;
    font-size: 54px;
    font-weight: 700;
    letter-spacing: 6px;
    color: var(--brand-green);
    line-height: 1;
  }
  .brand-dot {
    width: 20px; height: 20px;
    border-radius: 50%;
    background: var(--brand-green);
  }
  .brand-tagline {
    margin-top: 10px;
    font-size: 13px;
    font-weight: 700;
    letter-spacing: 3.4px;
    color: var(--tagline-dark);
  }
  .card--back-white .brand,
  .card--back-lime .brand,
  .card--back-photo .brand { top: 118px; }

  .card--front .brand { left: 22px; right: auto; top: 56px; text-align: left; }
  .card--front .brand-name { font-size: 34px; letter-spacing: 4px; gap: 8px; }
  .card--front .brand-dot { width: 13px; height: 13px; }
  .card--front .brand-tagline { margin-top: 6px; font-size: 10.5px; letter-spacing: 1.9px; color: var(--text-light); }

  .holder {
    position: absolute; right: 23px; top: 172px; text-align: right;
  }
  .holder-name { font-size: 18px; line-height: 22px; }
  .holder-role { font-size: 14px; line-height: 18px; }
  .divider {
    position: absolute; left: 24px; right: 23px; top: 215px;
    border-top: 1px solid var(--rule);
  }
  .contact-list {
    position: absolute; top: 232px;
    list-style: none;
    font-size: 15px;
    line-height: 21px;
  }
  .contact-list--phones { left: 24px; }
  .contact-list--web { left: 192px; }
  .contact-list li { display: flex; align-items: center; gap: 7px; }
  .contact-list svg { width: 12px; height: 12px; fill: var(--text-light); }
  .address {
    position: absolute; right: 23px; top: 219px;
    text-align: right; font-size: 14.5px; line-height: 18px;
    font-style: normal;
  }
</style>
</head>
<body>
  <p class="view-label" style="left:50px; top:33px;">Front</p>
  <p class="view-label" style="left:620px; top:33px;">Back - 1</p>
  <p class="view-label" style="left:50px; top:403px;">Back - 2</p>
  <p class="view-label" style="left:620px; top:403px;">Back - 3</p>

  <section class="card card--front">
    <div class="brand">
      <div class="brand-name"><span class="brand-dot"></span>CORELANE</div>
      <div class="brand-tagline">SMART IT, SIMPLY DELIVERED</div>
    </div>
    <div class="holder">
      <div class="holder-name">Your Name</div>
      <div class="holder-role">Designation</div>
    </div>
    <div class="divider"></div>
    <ul class="contact-list contact-list--phones">
      <li><svg viewBox="0 0 12 12" aria-hidden="true"><path d="M2.5 1 4.3 3.3 3.3 4.6c.6 1.5 1.7 2.6 3.2 3.2l1.3-1L10 8.6 9 10.8C5 10.5 1.5 7 1.2 3Z"/></svg>+12 345 67890</li>
      <li><svg viewBox="0 0 12 12" aria-hidden="true"><path d="M3 1h5v3H3Zm-2 4h10v5H1Zm2 1v1h2V6Z"/></svg>+12 345 67890</li>
    </ul>
    <ul class="contact-list contact-list--web">
      <li><svg viewBox="0 0 12 12" aria-hidden="true"><path d="M1 3h10v7H1Zm1 .8L6 7l4-3.2V4L6 7.3 2 4Z"/></svg>info@website.com</li>
      <li><svg viewBox="0 0 12 12" aria-hidden="true"><path d="M6 1a5 5 0 1 0 0 10A5 5 0 0 0 6 1Zm-.5 1.3v1.9H3.3a4 4 0 0 1 2.2-1.9Zm1 0a4 4 0 0 1 2.2 1.9H6.5ZM2.1 5.2h3.4v1.6H2.1a4 4 0 0 1 0-1.6Zm4.4 0h3.4a4 4 0 0 1 0 1.6H6.5ZM3.3 7.8h2.2v1.9a4 4 0 0 1-2.2-1.9Zm3.2 0h2.2a4 4 0 0 1-2.2 1.9Z"/></svg>www.website.com</li>
    </ul>
    <address class="address">#0000, Street Name<br>Area Name<br>Country Code</address>
  </section>

  <section class="card card--back-white">
    <div class="brand">
      <div class="brand-name"><span class="brand-dot"></span>CORELANE</div>
      <div class="brand-tagline">SMART IT, SIMPLY DELIVERED</div>
    </div>
  </section>

  <section class="card card--back-lime">
    <div class="brand">
      <div class="brand-name"><span class="brand-dot"></span>CORELANE</div>
      <div class="brand-tagline">SMART IT, SIMPLY DELIVERED</div>
    </div>
  </section>

  <section class="card card--back-photo">
    <div class="photo-fill" role="img" aria-label="Abstract blue technology background with glowing light rings, binary digits and a wireframe globe"></div>
    <div class="brand">
      <div class="brand-name"><span class="brand-dot"></span>CORELANE</div>
      <div class="brand-tagline">SMART IT, SIMPLY DELIVERED</div>
    </div>
  </section>
</body>
</html>
```